female esthetician looking for an impact business card

I an an expert in skin care industry with high experience in NYC.I want my business card to look professional , an impact at first look. I do want a combination between white and gold . I believe the font will be great if is gold.. The Fonts are also important. MIRABELA COSTINA (SKIN CARE BOUTIQUE)

THIS SHOULD BE THE BUSINESS NAME, and should be placed on th eback of the card.
IN front m, the name MIRABELA COSTINA - ESTHETCIAN

BY APPOINTMENTS ONLY: 518.240.7136

Target Market(s)

HIGH END CLIENTELE

Contact Information for Business Card

iT WILL BE on a luxury paper. I neeed the wow feeling

Requirements
Should not have
• pictures

```html
<!DOCTYPE html>
<html lang="en">
<head>
<meta charset="UTF-8">
<title>Mirabela Costina – Business Card</title>
<link rel="stylesheet" href="https://fonts.googleapis.com/css2?family=Cinzel:wght@400;500&display=swap">
<style>
  :root {
    --backdrop: #dddddd;
    --paper: #ffffff;
    --gold: #d2a36a;
    --gold-card: #d9ad7f;
    --ink-light: #ffffff;
  }
  * { margin: 0; padding: 0; box-sizing: border-box; }
  html, body {
    width: 1200px;
    height: 897px;
    overflow: hidden;
    background: var(--backdrop);
    font-family: "Cinzel", serif;
  }
  .canvas {
    position: relative;
    width: 1200px;
    height: 897px;
  }
  .card {
    position: absolute;
    left: 329px;
    width: 543px;
    height: 310px;
  }
  .card--front { top: 108px; background: var(--paper); color: var(--gold); }
  .card--back  { top: 479px; background: var(--gold-card); }

  .identity {
    position: absolute;
    left: 25px;
    top: 26px;
  }
  .identity__name {
    font-size: 19px;
    font-weight: 500;
    letter-spacing: 0.09em;
    line-height: 1;
  }
  .identity__role {
    margin-top: 6px;
    font-size: 12.5px;
    letter-spacing: 0.03em;
    line-height: 1;
  }
  .website {
    position: absolute;
    right: 25px;
    top: 28px;
    font-size: 12px;
    letter-spacing: 0.02em;
    line-height: 1;
  }
  .contact, .address {
    position: absolute;
    bottom: 24px;
    font-size: 13px;
    letter-spacing: 0.03em;
    line-height: 19px;
  }
  .contact { left: 25px; }
  .contact__email { font-size: 12px; }
  .address { right: 25px; text-align: right; }

  .back__name {
    position: absolute;
    left: 0;
    right: 0;
    top: 50%;
    transform: translateY(-38%);
    text-align: center;
    color: var(--ink-light);
    font-size: 29px;
    font-weight: 500;
    letter-spacing: 0.03em;
    line-height: 1;
  }
</style>
</head>
<body>
<main class="canvas">
  <section class="card card--front" aria-label="Card front">
    <div class="identity">
      <h1 class="identity__name">MIRABELA COSTINA</h1>
      <p class="identity__role">Skin care expert</p>
    </div>
    <p class="website">WWW.MIRABELACOSTINA.COM</p>
    <div class="contact">
      <p class="contact__phone">(518) 240-7136</p>
      <p class="contact__email">INFO@MIRABELACOSTINA.COM</p>
    </div>
    <address class="address" style="font-style: normal;">
      <p>218b Rosewell Street,</p>
      <p>Ashbury, NZ, 8042</p>
    </address>
  </section>

  <section class="card card--back" aria-label="Card back">
    <h2 class="back__name">MIRABELA COSTINA</h2>
  </section>
</main>
</body>
</html>
```